Book Cover Design: Backgammon - Copper Lantern Night Ledger

Book cover design for a self-published book to be sold on Brindle as a paperback as well as ebook.
The reader takes a quiz of 100 backgammon positions and then see how they fared versus 12 of the best players in the world. The pros then give explanations as to why they made their plays.

Th designs I had are a bit flat so far.

The special thing about this book is 12 of best in world taking the quiz before the reader. That is the attraction…

So how about design where photos of all 12 of them are showing within a backgammon board. You can leave the space for their pics and I insert later or you do once won contract.

But focus on the geniuses would be great, thank you!
Updates

Low design quality

Target Market(s)

Backgammon game enthusiasts

Requirements
Must have
• Picture of a backgammon board and idea quiz and top players in the world involved. Author’s name Oren Haskett
Nice to have
• Idea that 12 world class expert backgammon players all contributed to the book

```html
<!DOCTYPE html>
<html lang="en">
<head>
<meta charset="utf-8">
<title>Backgammon – Copper Lantern Night Ledger</title>
<link href="https://fonts.googleapis.com/css2?family=Luckiest+Guy&family=Poppins:wght@700;800&display=block" rel="stylesheet">
<style>
  :root {
    --wood-dark: #262120;
    --wood-mid: #443b36;
    --wood-light: #574e47;
    --title-cream: #ecebd9;
    --subtitle-orange: #e88c58;
    --label-white: #f4f1ea;
    --author-gold: #d9c48f;
    --board-cream: #f0eacb;
    --board-red: #e2553b;
    --board-frame: #2b2b2b;
  }
  html, body {
    margin: 0;
    padding: 0;
    overflow: hidden;
    background: #1a1816;
  }
  .cover {
    position: relative;
    width: 800px;
    height: 1200px;
    overflow: hidden;
  }
  .cover__backdrop {
    position: absolute;
    inset: 0;
    background:
      radial-gradient(ellipse at 30% 45%, var(--wood-light) 0%, transparent 60%),
      linear-gradient(180deg, var(--wood-dark) 0%, var(--wood-mid) 40%, var(--wood-mid) 65%, var(--wood-dark) 100%);
  }
  .cover__art {
    position: absolute;
    inset: 0;
    width: 800px;
    height: 1200px;
  }
  .cover__title {
    position: absolute;
    top: 52px;
    left: 0;
    width: 100%;
    margin: 0;
    text-align: center;
    font-family: "Luckiest Guy", "Poppins", sans-serif;
    font-weight: 800;
    font-synthesis: none;
    font-size: 94px;
    line-height: 1;
    letter-spacing: 1px;
    color: var(--title-cream);
  }
  .cover__subtitle {
    position: absolute;
    top: 170px;
    left: 0;
    width: 100%;
    margin: 0;
    text-align: center;
    font-family: "Poppins", sans-serif;
    font-weight: 700;
    font-size: 40px;
    line-height: 1;
    color: var(--subtitle-orange);
  }
  .tag {
    position: absolute;
    margin: 0;
    font-family: "Poppins", sans-serif;
    font-weight: 800;
    color: var(--label-white);
    text-transform: uppercase;
    line-height: 1.15;
    white-space: nowrap;
  }
  .tag--quizzes {
    left: 64px;
    top: 615px;
    font-size: 34px;
    transform: rotate(-13deg);
    transform-origin: left top;
  }
  .tag--players {
    left: 112px;
    top: 758px;
    font-size: 36px;
    transform: rotate(16deg);
    transform-origin: left top;
  }
  .cover__author {
    position: absolute;
    bottom: 30px;
    left: 0;
    width: 100%;
    margin: 0;
    text-align: center;
    font-family: "Poppins", sans-serif;
    font-weight: 800;
    font-size: 38px;
    letter-spacing: 1px;
    color: var(--author-gold);
  }
</style>
</head>
<body>
  <main class="cover">
    <div class="cover__backdrop" role="img" aria-label="Dark weathered wooden planks as the cover background"></div>

    <svg class="cover__art" viewBox="0 0 800 1200" xmlns="http://www.w3.org/2000/svg">
      <defs>
        <linearGradient id="boardTone" x1="0" y1="0" x2="1" y2="1">
          <stop offset="0" stop-color="var(--board-cream)"/>
          <stop offset="0.35" stop-color="#ecb49c"/>
          <stop offset="0.55" stop-color="var(--board-cream)"/>
          <stop offset="0.8" stop-color="#eaa48b"/>
          <stop offset="1" stop-color="var(--board-cream)"/>
        </linearGradient>
      </defs>

      <g class="board" role="img" aria-label="Photograph of a folding backgammon board with red and cream points, black and red checkers and a pair of dice">
        <polygon points="336,428 800,196 800,960 478,1042" fill="var(--board-frame)"/>
        <polygon points="350,434 800,210 800,948 486,1026" fill="url(#boardTone)"/>
      </g>

      <g class="callouts" fill="none" stroke="var(--label-white)" stroke-width="4" stroke-dasharray="7 7" stroke-linecap="round">
        <rect class="callout-frame" x="45" y="598" width="305" height="85" rx="16" transform="rotate(-13 45 598)"/>
        <rect class="callout-frame" x="90" y="745" width="415" height="165" rx="18" transform="rotate(16 90 745)"/>
        <path class="callout-arrow" d="M474 444 C 420 405, 310 400, 262 430 C 220 456, 250 500, 212 516"/>
        <path class="callout-arrow" d="M488 968 C 500 945, 530 950, 520 975 C 540 995, 600 995, 640 982"/>
      </g>
      <g fill="none" stroke="var(--label-white)" stroke-width="4" stroke-linecap="round">
        <polyline points="196,498 208,520 230,512"/>
      </g>
    </svg>

    <h1 class="cover__title">BACKGAMMON</h1>
    <p class="cover__subtitle">COPPER LANTERN NIGHT LEDGER</p>

    <p class="tag tag--quizzes">100 Quizzes</p>
    <p class="tag tag--players">Moves of<br>Top 12 Players<br>in the World</p>

    <p class="cover__author">OREN HASKETT</p>
  </main>
</body>
</html>
```